Website for IT consulting Company

I need a website upgrade, the existing site content is ok, I would also like to add a testimonial page, the site should be something that is easy for us to update content. You use the content from www.kelvanbrook.com as an example. I will also post update logo and artwork. I also need a contact form with some type of validation or captcha.

I added Coded to the Project

Please omit Address maps

Target Market(s)

small business, service oriented companies. We provide IT Consulting, support and mangement

Industry/Entity Type

Information Technology

Coding

Number of Pages Required

1 page

Font styles to use
Serif
Sans Serif

Requirements
Must have
• Contain logo attached, and content from existing web site www.kelvanbrook.com.
• Also need to update content easily, and be movable to different platforms.
• There is a catch phrase
• "Let us worry about your technology…” “ so you don’t have to!”
• Should be included.
Nice to have
• Testimonial page, Project page where we can post new and past projects and pictures
Should not have
• none

```html
<!DOCTYPE html>
<html lang="en">
<head>
<meta charset="utf-8">
<title>Kelvanbrook Group, Inc</title>
<link href="https://fonts.googleapis.com/css2?family=Exo+2:ital,wght@0,600;0,700;0,800;1,700;1,800&family=Arimo:ital,wght@0,400;0,700;1,400&family=Open+Sans:wght@400;600&display=swap" rel="stylesheet">
<style>
:root{
  --orange:#f0922b;
  --orange-dark:#e8781f;
  --ink:#1c1c1c;
  --text:#2a2a2a;
  --grey-band:#e9e9e9;
  --grey-mid:#8a8a8a;
  --grey-icon:#6d6d6d;
  --navy:#1f4e86;
  --footer:#3a3634;
  --copyright:#7a7876;
}
*{box-sizing:border-box;margin:0;padding:0}
html,body{width:1200px;height:2276px;overflow:hidden;background:#fff}
body{font-family:"Arimo",Arial,sans-serif;color:var(--text);position:relative}
.heading{font-family:"Exo 2",sans-serif;font-style:italic;font-weight:800;letter-spacing:1px}
.heading .accent{color:var(--orange)}

.topbar{height:36px;background:#050505;display:flex;justify-content:flex-end;gap:8px;padding:4px 57px 0 0}
.topbar .social-square{width:28px;height:28px;background:#cfcfcf;border-radius:2px}

.site-header{height:88px;display:flex;align-items:center;justify-content:space-between;padding:0 90px 0 80px}
.brand{display:flex;align-items:center;gap:14px}
.brand .mark{width:44px;height:44px;background:var(--orange)}
.brand .name{font-family:"Exo 2",sans-serif;font-weight:800;font-size:46px;color:#8c8c8c;letter-spacing:1px}
.header-phone{display:flex;align-items:center;gap:14px;font-family:"Exo 2",sans-serif;font-style:italic;font-weight:700;font-size:21px;color:#666}
.header-phone .icon{width:28px;height:28px;background:var(--orange);border-radius:3px;display:flex;align-items:center;justify-content:center}

.main-nav{height:57px;background:linear-gradient(90deg,var(--orange),var(--orange-dark));display:flex;align-items:stretch;padding-left:92px}
.main-nav a{font-family:"Exo 2",sans-serif;font-style:italic;font-weight:800;font-size:19px;color:#fff;text-decoration:none;display:flex;align-items:center;letter-spacing:.5px}
.main-nav a.active{background:#050505;padding:0 8px;margin-right:56px}
.main-nav a+a{margin-right:64px}

.hero{position:relative;height:534px;background:linear-gradient(100deg,#b9c6cf 0%,#e6e6e3 30%,#f2f0ec 50%,#4f5560 72%,#c9d4dc 100%)}
.hero-tagline{position:absolute;left:0;right:0;bottom:0;height:58px;background:rgba(40,40,40,.82);display:flex;align-items:center;justify-content:center;font-size:33px;color:#fff}

.about{position:relative;height:426px}
.about-title{position:absolute;left:84px;top:62px;font-size:29px;color:var(--ink)}
.about-title::after{content:"";position:absolute;left:0;bottom:-14px;width:76px;height:2px;background:var(--orange)}
.about-copy{position:absolute;left:82px;top:133px;width:630px;font-size:14.5px;line-height:26px;color:var(--ink)}
.pillar{position:absolute;top:288px;display:flex;gap:18px}
.pillar .badge{width:70px;height:70px;border-radius:8px;background:linear-gradient(#9a9a9a,#5c5c5c);border:3px solid #ddd;display:flex;align-items:center;justify-content:center}
.pillar h3{font-family:"Open Sans",sans-serif;font-weight:600;font-size:20px;color:var(--ink);margin-top:2px}
.pillar p{font-size:14px;line-height:26px;color:var(--ink)}

.inquiry{position:absolute;left:765px;top:48px;width:355px;height:325px;background:#ececec;border:1px solid #d2d2d2}
.inquiry .tab{position:absolute;left:48px;top:-12px;width:260px;height:44px;background:linear-gradient(#9a9a9a,#5b5b5b);border:3px solid #fff;box-shadow:0 1px 3px rgba(0,0,0,.3);display:flex;align-items:center;justify-content:center;font-family:"Exo 2",sans-serif;font-style:italic;font-weight:700;font-size:20px;color:#fff}
.inquiry form{position:absolute;left:20px;top:52px;width:314px}
.inquiry .field{display:block;width:100%;height:34px;margin-bottom:8px;background:#fff;border:1px solid #d8d8d8;border-radius:3px;font-family:"Open Sans",sans-serif;font-size:12px;color:#555;padding:0 10px;line-height:32px}
.inquiry .call{text-align:center;margin-top:14px;font-family:"Exo 2",sans-serif;font-style:italic;font-weight:700;font-size:21px;color:var(--ink)}
.inquiry .call span{color:var(--orange);font-weight:600;font-size:17px;margin-right:10px}
.inquiry .submit{display:block;margin:10px auto 0;width:124px;height:34px;background:var(--orange);color:#fff;border:0;font-family:"Exo 2",sans-serif;font-style:italic;font-weight:800;font-size:18px}

.services{height:405px;background:var(--grey-band);position:relative}
.services .heading{position:absolute;top:40px;width:100%;text-align:center;font-size:31px;color:var(--ink)}
.service-card{position:absolute;top:153px;width:316px;height:182px;background:#fff;border-radius:10px;box-shadow:0 5px 6px rgba(0,0,0,.22);text-align:center}
.service-card .icon{position:absolute;left:121px;top:-34px;width:73px;height:73px;border-radius:4px;display:flex;align-items:center;justify-content:center}
.service-card h4{margin-top:70px;font-family:"Exo 2",sans-serif;font-style:italic;font-weight:700;font-size:15px;color:#444;letter-spacing:.5px}
.service-card p{margin:14px auto 0;width:250px;font-size:13px;line-height:20px;color:#333}
.service-card .more{position:absolute;left:145px;bottom:-4px;width:26px;height:22px;color:#fff;font-weight:700;font-size:18px;line-height:22px}
.is-orange{background:var(--orange)}
.is-grey{background:linear-gradient(#9a9a9a,#5e5e5e)}

.testimonials{height:358px;position:relative}
.testimonials .heading{position:absolute;top:55px;width:100%;text-align:center;font-size:31px;color:var(--ink)}
.testimonials .rule{position:absolute;left:453px;top:103px;width:294px;height:1px;background:#cfcfcf}
.testimonials .rule::after{content:"";position:absolute;left:124px;top:-1px;width:40px;height:3px;background:var(--navy)}
.quote{position:absolute;left:205px;top:146px;width:790px;text-align:center;font-style:italic;font-size:15.5px;line-height:30px;color:var(--ink)}
.quote::before,.quote::after{font-family:Georgia,serif;font-size:36px;color:#999;position:relative}
.quote::before{content:"\201C";position:absolute;left:0;top:-4px}
.quote::after{content:"\201D";top:14px;margin-left:10px}
.author{position:absolute;top:260px;width:100%;text-align:center}
.author .who{font-weight:700;font-size:17px;color:var(--navy)}
.author .where{font-weight:700;font-size:15px;color:#222;margin-top:6px}
.arrow{position:absolute;top:170px}

.site-footer{position:relative;height:326px;background:linear-gradient(180deg,#4a4542 0%,var(--footer) 60%,#2c2a2a 100%)}
.footer-col{position:absolute;top:52px;color:#fff}
.footer-col h5{font-family:"Arimo",sans-serif;font-weight:400;font-size:20px;padding-bottom:12px;border-bottom:1px solid #6a6563;width:195px}
.footer-col h5 span{color:var(--orange)}
.quick-links{list-style:none;margin-top:12px}
.quick-links li{font-size:14px;line-height:25px;padding-left:15px;position:relative}
.quick-links li::before{content:"";position:absolute;left:0;top:10px;width:4px;height:4px;border-radius:50%;background:var(--orange)}
.contact-lines{margin-top:12px;font-size:14px;line-height:21px}
.contact-lines .row{display:flex;align-items:center;gap:10px;margin-top:14px}
.social-list{margin-top:18px}
.social-list .row{display:flex;align-items:center;gap:14px;height:44px;font-size:14px}
.social-list .square{width:28px;height:28px;background:#cfcfcf;border-radius:2px}

.copyright{height:46px;background:linear-gradient(#8c8a88,#6b6967);color:#fff;font-weight:700;font-size:15px;display:flex;align-items:center;justify-content:center}
</style>
</head>
<body>

<div class="topbar">
  <span class="social-square"></span><span class="social-square"></span><span class="social-square"></span><span class="social-square"></span>
</div>

<header class="site-header">
  <div class="brand"><span class="mark"></span><span class="name">KELVANBROOK</span></div>
  <div class="header-phone">
    <span class="icon"><svg width="16" height="16" viewBox="0 0 24 24"><path fill="#2a2a2a" d="M6.6 10.8a15 15 0 0 0 6.6 6.6l2.2-2.2c.3-.3.7-.4 1-.2 1.1.4 2.3.6 3.6.6.6 0 1 .4 1 1V20c0 .6-.4 1-1 1A17 17 0 0 1 3 4c0-.6.4-1 1-1h3.5c.6 0 1 .4 1 1 0 1.3.2 2.5.6 3.6.1.3 0 .7-.2 1z"/></svg></span>
    (555) 014-2270
  </div>
</header>

<nav class="main-nav">
  <a class="active" href="#">HOME</a>
  <a href="#">ABOUT US</a>
  <a href="#">SERVICES</a>
  <a href="#">SUPPORT</a>
  <a href="#">CLIENTS</a>
  <a href="#">CAREERS</a>
  <a href="#">CONTACT US</a>
</nav>

<section class="hero" role="img" aria-label="Photo of a consulting team smiling around a meeting table in a bright office">
  <div class="hero-tagline heading">Let Us Worry About Your Technology...&nbsp;<span class="accent">So You Don’t Have To!</span></div>
</section>

<section class="about">
  <h2 class="about-title heading">ABOUT&nbsp; KELVANBROOK <span class="accent">GROUP, INC</span></h2>
  <p class="about-copy">Kelvanbrook is a technology solution provider based in Fairhaven, Texas. Our goal is to make technology a non-issue for individuals and small to medium size businesses ranging from 5 to 150 Users. Kelvanbrook has the experience, the tools, high-level technology solutions and training to power your business and your work force. We understand that all business’s have one goal in common!</p>

  <div class="pillar" style="left:80px">
    <div class="badge"><svg width="40" height="40" viewBox="0 0 40 40" fill="none" stroke="#fff" stroke-width="3"><circle cx="19" cy="19" r="14"/><circle cx="19" cy="19" r="6"/><path d="M22 22l12 12"/></svg></div>
    <div><h3>Our Mission</h3><p>Lorem ipsum dolor a sit amet,<br>consectetuer adipisc....{+}</p></div>
  </div>
  <div class="pillar" style="left:406px">
    <div class="badge"><svg width="40" height="40" viewBox="0 0 40 40" fill="none" stroke="#fff" stroke-width="2.5"><path d="M14 26c-3-2-5-5-5-9a11 11 0 0 1 22 0c0 4-2 7-5 9v4H14z"/><path d="M15 34h10"/><path d="M20 2v3M6 8l2 2M34 8l-2 2"/></svg></div>
    <div><h3>Our Vision</h3><p>Lorem ipsum dolor a sit amet,<br>consectetuer adipisc....{+}</p></div>
  </div>

  <aside class="inquiry">
    <div class="tab">Quick Inquiry</div>
    <form>
      <span class="field">First Name</span>
      <span class="field">Last Name</span>
      <span class="field">Email</span>
      <span class="field">Phone</span>
      <p class="call"><span>Or</span>Call 1-888-555-0192</p>
      <button class="submit" type="button">Submit</button>
    </form>
  </aside>
</section>

<section class="services">
  <h2 class="heading">OUR <span class="accent">SERVICES</span></h2>

  <article class="service-card" style="left:77px">
    <div class="icon is-orange"><svg width="44" height="44" viewBox="0 0 44 44" fill="none" stroke="#fff" stroke-width="2.5"><circle cx="22" cy="22" r="5"/><path d="M22 4v13M22 27v13M4 22h13M27 22h13M9 9l9 9M26 26l9 9M35 9l-9 9M18 26l-9 9"/></svg></div>
    <h4>Managed IT Solutions</h4>
    <p>Duis autem vel eum iriure do in hendrerit in vulputate Duis autem he....</p>
    <span class="more is-orange">+</span>
  </article>
  <article class="service-card" style="left:441px">
    <div class="icon is-grey"><svg width="44" height="44" viewBox="0 0 44 44" fill="none" stroke="#fff" stroke-width="2.5"><circle cx="22" cy="18" r="10"/><path d="M8 40c2-8 8-11 14-11s12 3 14 11M10 18a12 12 0 0 1 24 0M30 26l-6 2"/></svg></div>
    <h4>Remote Diagnostic &amp; Support</h4>
    <p>Duis autem vel eum iriure do in hendrerit in vulputate Duis autem he....</p>
    <span class="more is-grey">+</span>
  </article>
  <article class="service-card" style="left:805px">
    <div class="icon is-grey"><svg width="46" height="36" viewBox="0 0 46 36" fill="#fff"><path d="M2 10h10a4 4 0 1 1 8 0h3v8a4 4 0 1 1 0 8v8H2z"/><path d="M25 10h8a4 4 0 1 1 8 0h3v24H25v-8a4 4 0 1 0 0-8z" opacity=".85"/></svg></div>
    <h4>Infrastructure Design &amp; Installation</h4>
    <p>Duis autem vel eum iriure do in hendrerit in vulputate Duis autem he....</p>
    <span class="more is-grey">+</span>
  </article>
</section>

<section class="testimonials">
  <h2 class="heading">CLIENTS <span class="accent">TESTIMONIALS</span></h2>
  <div class="rule"></div>
  <svg class="arrow" style="left:108px" width="32" height="56" viewBox="0 0 32 56"><path d="M30 2L2 28l28 26" fill="none" stroke="#999" stroke-width="1.5"/></svg>
  <blockquote class="quote">Lorem ipsum dolor sit amet, consectetuer adipiscing elit, sed diam nonummy nibh euismod tinciduntol ut laoreet dolore magna aliquam erat volutpat. Ut wisi enim ad minim veniam, quis nostrud exercimori mornkle tation ullamcorper suscipit lobortis nisl ut aliquip ex ea commodo consequat.</blockquote>
  <svg class="arrow" style="left:1050px" width="32" height="56" viewBox="0 0 32 56"><path d="M2 2l28 26L2 54" fill="none" stroke="#999" stroke-width="1.5"/></svg>
  <div class="author"><p class="who">Morgan R.</p><p class="where">Lakeview, CA</p></div>
</section>

<footer class="site-footer" role="img" aria-label="Dim evening city skyline behind the footer columns">
  <div class="footer-col" style="left:88px">
    <h5>Quick <span>Links</span></h5>
    <ul class="quick-links">
      <li>Home</li><li>About Us</li><li>Services</li><li>Support</li><li>Clients</li><li>Careers</li><li>Contact Us</li>
    </ul>
  </div>
  <div class="footer-col" style="left:336px">
    <h5 style="border:0">Contact <span>Details</span></h5>
    <div class="contact-lines">
      <p>Kelvanbrook Group, Inc.</p>
      <p style="margin-top:6px">418 Marlow Ave.<br>Fairhaven, Texas 77031</p>
      <div class="row"><svg width="14" height="14" viewBox="0 0 24 24"><path fill="#f0922b" d="M6.6 10.8a15 15 0 0 0 6.6 6.6l2.2-2.2c.3-.3.7-.4 1-.2 1.1.4 2.3.6 3.6.6.6 0 1 .4 1 1V20c0 .6-.4 1-1 1A17 17 0 0 1 3 4c0-.6.4-1 1-1h3.5c.6 0 1 .4 1 1 0 1.3.2 2.5.6 3.6.1.3 0 .7-.2 1z"/></svg>(555) 014-2270</div>
      <div class="row"><svg width="14" height="14" viewBox="0 0 24 24" fill="#f0922b"><rect x="6" y="2" width="12" height="6"/><rect x="2" y="9" width="20" height="9" rx="2"/><rect x="6" y="15" width="12" height="7" fill="#3a3634" stroke="#f0922b" stroke-width="2"/></svg>(555) 014-2270</div>
      <div class="row"><svg width="14" height="11" viewBox="0 0 24 18"><rect width="24" height="18" fill="#f0922b"/><path d="M0 0l12 10L24 0" fill="none" stroke="#3a3634" stroke-width="2"/></svg>info@kelvanbrook.com</div>
    </div>
  </div>
  <div class="footer-col" style="left:645px">
    <h5 style="border:0">Get <span>Social</span></h5>
    <div class="social-list">
      <div class="row"><span class="square"></span>Friendline</div>
      <div class="row"><span class="square"></span>Chirper</div>
      <div class="row"><span class="square"></span>Circlenet</div>
      <div class="row"><span class="square"></span>Worklink</div>
    </div>
  </div>
</footer>

<div class="copyright">Copyright © 2017 Kelvanbrook Group, Inc. All Rights Reserved.</div>

</body>
</html>
```